Furniture & Lighting Wholesaler Needs a Product Catalogue/Look Book

Our company, Vostre Merchant Co, imports quality hand-made furniture, lighting and decor from South Africa. Our products are well-designed and are designed to be used in up-market hotels and homes. Our primary customers are small- to medium-size retail shops.
We require a +/- 14-16 page look book (concept as per attached image) that will be used both in hard-copy and online. We have all of the necessary high-res images, descriptions/text etc. We need you to propose several design concepts from which we can choose, and then execute the design.
Please visit our website www.vostremerchant.example to see the products and their descriptions, as well as to get a feel for our style. Thank you for looking at our project!
Target Market(s)
Boutique Furniture Stores; Interior Designers
Industry/Entity Type
It Company
Font styles to use
Other font styles liked:
- Bauer Bodini and Open Sans Condensed
Look and feel
Each slider illustrates characteristics of the customer's brand and the style your logo design should communicate.

```html
<!DOCTYPE html>
<html lang="en">
<head>
<meta charset="utf-8">
<title>Vostre Merchant Co — Look Book, pages 10–11</title>
<link rel="stylesheet" href="https://fonts.googleapis.com/css2?family=Open+Sans:wght@300;400;600;700&display=swap">
<style>
  :root {
    --bg: #d9d9d9;
    --paper: #ffffff;
    --gold: #a99b6c;
    --ink: #3b3b3b;
    --slate: #4a4a4a;
    --box: #e2e2e2;
    --halo: #ececec;
    --photo-top: #55524c;
    --photo-bottom: #77736a;
  }
  * { box-sizing: border-box; margin: 0; padding: 0; }
  html, body { width: 1200px; height: 800px; overflow: hidden; }
  body { background: var(--bg); font-family: "Open Sans", sans-serif; color: var(--ink); }

  .spread {
    position: absolute; left: 20px; top: 195px; width: 1160px; height: 410px;
    display: flex; box-shadow: 0 10px 30px rgba(0,0,0,.18);
  }
  .page { position: relative; width: 580px; height: 410px; background: var(--paper); overflow: hidden; }
  .page--left { background: linear-gradient(to right, #fff 92%, #f0f0f0); }
  .page--right { background: linear-gradient(to left, #fff 92%, #f0f0f0); }

  .edge-band { position: absolute; width: 24px; background: var(--gold); }
  .page--left .edge-band { left: 0; top: 230px; height: 180px; border-top-right-radius: 24px; }
  .page--right .edge-band { right: 0; top: 0; height: 165px; border-bottom-left-radius: 24px; }
  .folio {
    position: absolute; width: 34px; height: 30px; background: var(--slate);
    color: var(--gold); font-size: 9px; display: flex; align-items: center; justify-content: center;
  }
  .page--left .folio { left: 0; bottom: 0; border-top-right-radius: 14px; }
  .page--right .folio { right: 0; top: 165px; border-bottom-left-radius: 14px; }

  .photo-halo { position: absolute; background: var(--halo); border-radius: 30px; }
  .photo {
    position: absolute; border: 2px solid var(--gold); border-radius: 24px;
    box-shadow: 0 0 0 5px #fff;
    background: linear-gradient(180deg, var(--photo-top), var(--photo-bottom));
  }

  .product-name { position: absolute; color: var(--gold); font-size: 14px; font-weight: 400; letter-spacing: .3px; white-space: nowrap; }
  .product-intro { position: absolute; font-size: 7px; font-weight: 700; line-height: 1.25; width: 150px; }
  .product-points { position: absolute; font-size: 7.5px; line-height: 1.45; list-style: none; white-space: nowrap; }
  .product-points li::before { content: "•"; margin-right: 8px; }

  .price {
    position: absolute; background: var(--gold); color: #fff; font-size: 15px; font-weight: 400;
    padding: 2px 10px; width: 92px; border-top: 2px solid var(--slate);
  }
  .spec-box { position: absolute; background: var(--box); width: 86px; height: 38px; }

  .footer-web { position: absolute; bottom: 10px; font-size: 6.5px; color: #777; display: flex; align-items: center; gap: 6px; }
  .footer-web .mark { width: 9px; height: 9px; border: 2px solid var(--slate); }
</style>
</head>
<body>
<main class="spread">

  <section class="page page--left">
    <div class="edge-band"></div>
    <div class="folio">10</div>

    <article class="product">
      <div class="photo-halo" style="left:32px;top:28px;width:216px;height:230px"></div>
      <div class="photo" style="left:45px;top:40px;width:190px;height:205px" role="img" aria-label="Product photo: cluster of fringed pendant lamps"></div>
      <h2 class="product-name" style="left:60px;top:282px">PRODUCT NAME</h2>
      <p class="product-intro" style="left:60px;top:303px">Faccupia ipsim excearum rae expligent lam qui occupia rchicie ndesequ iatur</p>
      <ul class="product-points" style="left:60px;top:325px">
        <li>Sint labor sinvelluptat ulles cil</li>
        <li>Es maximus si num ad etus</li>
        <li>Acersped moluptaquate</li>
        <li>Eelia cus cuptatem voles</li>
        <li>Bos es doluptam invechicis</li>
        <li>Wuidi dollorestrum</li>
        <li>Cus de nones mos ma idit res</li>
      </ul>
      <div class="price" style="left:225px;top:225px">$59.99</div>
      <div class="spec-box" style="left:231px;top:258px"></div>
      <div class="spec-box" style="left:231px;top:300px"></div>
    </article>

    <article class="product">
      <div class="photo-halo" style="left:315px;top:14px;width:228px;height:190px"></div>
      <div class="photo" style="left:327px;top:25px;width:205px;height:170px" role="img" aria-label="Product photo: carved wooden table beneath a chandelier"></div>
      <h2 class="product-name" style="left:332px;top:212px">PRODUCT NAME</h2>
      <p class="product-intro" style="left:332px;top:232px">Faccupia ipsim excearum rae expligent lam qui occupia rchicie ndesequ iatur</p>
      <ul class="product-points" style="left:332px;top:254px">
        <li>Sint labor sinvelluptat ulles cil</li>
        <li>Es maximus si num ad etus</li>
        <li>Acersped moluptaquate</li>
        <li>Eelia cus cuptatem voles</li>
        <li>Bos es doluptam invechicis</li>
        <li>Wuidi dollorestrum magnam</li>
        <li>Aut que ex enist fugitio restrunt</li>
      </ul>
      <div class="price" style="left:478px;top:196px">$59.99</div>
      <div class="spec-box" style="left:484px;top:228px"></div>
      <div class="spec-box" style="left:484px;top:270px"></div>
    </article>

    <div class="footer-web" style="right:30px"><span class="mark"></span>www.vostremerchant.example</div>
  </section>

  <section class="page page--right">
    <div class="edge-band"></div>
    <div class="folio">11</div>

    <article class="product">
      <div class="photo-halo" style="left:28px;top:14px;width:225px;height:190px"></div>
      <div class="photo" style="left:40px;top:25px;width:200px;height:170px" role="img" aria-label="Product photo: fringed pendant lamps"></div>
      <h2 class="product-name" style="left:45px;top:212px">PRODUCT NAME</h2>
      <p class="product-intro" style="left:45px;top:232px">Faccupia ipsim excearum rae expligent lam qui occupia rchicie ndesequ iatur</p>
      <ul class="product-points" style="left:45px;top:254px">
        <li>Sint labor sinvelluptat ulles cil</li>
        <li>Es maximus si num ad etus</li>
        <li>Acersped moluptaquate</li>
        <li>Eelia cus cuptatem voles</li>
        <li>Bos es doluptam invechicis</li>
        <li>Wuidi dollorestrum</li>
        <li>Cus de nones mos ma idit res</li>
      </ul>
      <div class="price" style="left:200px;top:196px">$59.99</div>
      <div class="spec-box" style="left:206px;top:228px"></div>
      <div class="spec-box" style="left:206px;top:270px"></div>
    </article>

    <article class="product">
      <div class="photo-halo" style="left:290px;top:14px;width:230px;height:175px"></div>
      <div class="photo" style="left:302px;top:25px;width:205px;height:155px" role="img" aria-label="Product photo: carved wooden dining table"></div>
      <h2 class="product-name" style="left:305px;top:196px">PRODUCT NAME</h2>
      <p class="product-intro" style="left:305px;top:216px">Faccupia ipsim excearum rae expligent lam qui occupia rchicie ndesequ iatur</p>
      <ul class="product-points" style="left:305px;top:238px">
        <li>Sint labor sinvelluptat ulles cil</li>
        <li>Es maximus si num ad etus</li>
        <li>Acersped moluptaquate</li>
        <li>Eelia cus cuptatem voles</li>
        <li>Bos es doluptam invechicis</li>
        <li>Wuidi dollorestrum magnam</li>
        <li>Aut que ex enist fugitio restrunt</li>
      </ul>
      <div class="price" style="left:449px;top:180px">$59.99</div>
      <div class="spec-box" style="left:455px;top:212px"></div>
      <div class="spec-box" style="left:455px;top:254px"></div>
    </article>

    <div class="footer-web" style="left:30px"><span class="mark"></span>www.vostremerchant.example</div>
  </section>

</main>
</body>
</html>
```